business card - Helicopter Flight Services, Flight School, etc.

We need a business card design for a new helicopter service.

We offer Helicopter Flight Services, Aerial Filming & Photography, Flight School, and Helicopter Tours. In that order.

Summit BladeAir, Inc.
Dennis Tollerby
SummitBladeair@Kestmail.com
626-418-7352

Based at the Brenwick Airport in Van Nuys, CA. The final design should communicate integrity and safety. Pictures or logos at your discretion.

Card back side - surprise me.

```html
<!DOCTYPE html>
<html lang="en">
<head>
<meta charset="utf-8">
<title>Summit BladeAir, Inc. – Business Card</title>
<link rel="stylesheet" href="https://fonts.googleapis.com/css2?family=Old+Standard+TT:wght@400&family=Noto+Sans:wght@400&display=swap">
<style>
  :root {
    --backdrop: #c4c4c4;
    --card-light-top: #d3d3d3;
    --card-light-mid: #ececec;
    --card-dark: #000000;
    --accent-blue: #3c3fae;
    --wordmark-blue: #6a6ec8;
    --wordmark-light: #c9cbf0;
    --text-light: #f2f2f2;
    --divider: #6b6b6b;
  }
  * { margin: 0; padding: 0; box-sizing: border-box; }
  html, body {
    width: 1189px; height: 1200px; overflow: hidden;
    background: var(--backdrop);
  }
  .canvas { position: relative; width: 1189px; height: 1200px; }
  .card {
    position: absolute; left: 140px; width: 918px; height: 524px;
    box-shadow: 0 6px 14px rgba(0,0,0,0.35);
    overflow: hidden;
  }
  .card--front { top: 45px; background: var(--card-dark); }
  .card--back { top: 624px; background: var(--card-dark); }

  .front__header {
    position: absolute; left: 0; top: 0; width: 100%; height: 250px;
    background: radial-gradient(ellipse at 50% 85%, var(--card-light-mid) 0%, var(--card-light-top) 75%);
  }
  .front__stripe {
    position: absolute; left: 0; top: 250px; width: 100%; height: 24px;
    background: var(--accent-blue);
  }
  .wordmark {
    position: absolute; left: 0; width: 100%; text-align: center;
    font-family: "Old Standard TT", "Century Schoolbook", serif;
    font-weight: 400; white-space: nowrap;
  }
  .front__wordmark { top: 116px; font-size: 58px; line-height: 1; color: var(--wordmark-blue); }
  .back__wordmark { top: 218px; font-size: 60px; line-height: 1; color: var(--wordmark-light); }

  .contact-name {
    position: absolute; left: 97px; top: 360px;
    font-family: "Noto Sans", Arial, sans-serif; font-size: 29px;
    color: var(--text-light); white-space: nowrap;
  }
  .front__divider {
    position: absolute; left: 411px; top: 304px; width: 2px; height: 173px;
    background: var(--divider);
  }
  .contact-list {
    position: absolute; left: 458px; top: 324px; list-style: none;
    font-family: "Noto Sans", Arial, sans-serif; font-size: 24px;
    color: var(--text-light); line-height: 37px;
  }
  .contact-list li { position: relative; padding-left: 40px; white-space: nowrap; }
  .contact-list svg { position: absolute; left: 0; top: 9px; width: 18px; height: 18px; }

  .tagline {
    position: absolute; left: 0; top: 296px; width: 100%; text-align: center;
    font-family: "Noto Sans", Arial, sans-serif; font-size: 26px;
    color: var(--text-light);
  }
</style>
</head>
<body>
<div class="canvas">
  <section class="card card--front">
    <div class="front__header"></div>
    <div class="front__stripe"></div>
    <h1 class="wordmark front__wordmark">Summit BladeAir, Inc.</h1>
    <p class="contact-name">Dennis Tollerby</p>
    <div class="front__divider"></div>
    <ul class="contact-list">
      <li>
        <svg viewBox="0 0 18 18" aria-hidden="true"><rect width="18" height="18" fill="#f2f2f2"/><path d="M5 3.5c1 0 1.6 2.3 1.1 2.9L5.4 7.2c.7 1.8 2 3.2 3.6 4l.9-.8c.6-.5 2.8.3 2.8 1.2v1.6c0 .6-.6 1.1-1.4 1-4.5-.6-7.8-4.2-8.2-8.5C3 4.1 3.7 3.5 5 3.5z" fill="#000"/></svg>
        626-418-7352
      </li>
      <li>
        <svg viewBox="0 0 18 18" aria-hidden="true"><rect width="18" height="18" fill="#f2f2f2"/><rect x="3" y="5" width="12" height="8" fill="none" stroke="#000" stroke-width="1.4"/><path d="M3 5l6 5 6-5" fill="none" stroke="#000" stroke-width="1.4"/></svg>
        SummitBladeair@Kestmail.com
      </li>
      <li>
        <svg viewBox="0 0 18 18" aria-hidden="true"><rect width="18" height="18" fill="#f2f2f2"/><path d="M9 3.5a3.6 3.6 0 0 0-3.6 3.6C5.4 10 9 14.5 9 14.5s3.6-4.5 3.6-7.4A3.6 3.6 0 0 0 9 3.5z" fill="#000"/><circle cx="9" cy="7.1" r="1.3" fill="#f2f2f2"/></svg>
        2307 W. Larkspur Ave. Ste.B
      </li>
      <li>Halden, CA 90417</li>
    </ul>
  </section>

  <section class="card card--back">
    <h2 class="wordmark back__wordmark">Summit BladeAir, Inc.</h2>
    <p class="tagline">Airport · Tour guide · Heliport</p>
  </section>
</div>
</body>
</html>
```